New business card/stationary for a consulting company

I am looking for a clean and very professional looking business card for my consulting company as well as corresponding stationary. I am uploading our logo. I like simple and powerful for the feel. No graphics but I am open on everything else. Below is my contact information but would like the final to be in a version I can add my employees information into and print. Thank you.

Daniel Whitcombe
dan@ferncliffadvisory.com
2870 North 9th Avenue, Summit Floor, Elm Ridge, Illinois 60531
www.ferncliffadvisory.com

Industry/Entity Type

Consulting

Contact Information for Business Card

Daniel Whitcombe
dan@ferncliffadvisory.com
www.ferncliffadvisory.com

Font styles to use
Serif
Sans Serif

Requirements
Must have
• Our logo and the business card details.
Nice to have
• our website www.ferncliffadvisory.com

```html
<!DOCTYPE html>
<html lang="en">
<head>
<meta charset="utf-8">
<title>Ferncliff Advisory – Business Card</title>
<link rel="stylesheet" href="https://fonts.googleapis.com/css2?family=Montserrat:wght@300;400&family=Source+Sans+3:wght@400;600;700&display=swap">
<style>
  :root {
    --navy: #1b1890;
    --navy-deep: #14117a;
    --paper: #ffffff;
    --backdrop: #e4e5ea;
    --card-w: 560px;
    --card-h: 320px;
  }
  * { box-sizing: border-box; margin: 0; padding: 0; }
  html, body {
    width: 1200px;
    height: 900px;
    overflow: hidden;
    background: var(--backdrop);
  }
  .canvas {
    width: 1200px;
    height: 900px;
    display: flex;
    flex-direction: column;
    align-items: center;
    justify-content: center;
    gap: 60px;
  }
  .card {
    width: var(--card-w);
    height: var(--card-h);
    background: var(--paper);
    box-shadow: 0 10px 28px rgba(20, 20, 60, 0.18);
    position: relative;
    overflow: hidden;
  }
  .brand {
    display: flex;
    flex-direction: column;
    align-items: center;
    gap: 12px;
  }
  .brand-square {
    width: 30px;
    height: 30px;
    background: var(--navy);
  }
  .brand-name {
    font-family: "Montserrat", sans-serif;
    font-weight: 300;
    font-size: 28px;
    letter-spacing: 1px;
    color: var(--navy);
    text-transform: uppercase;
    white-space: nowrap;
  }
  .card-front {
    display: flex;
    align-items: center;
    justify-content: center;
  }
  .card-back { display: flex; flex-direction: column; }
  .band-top {
    height: 168px;
    background: var(--navy);
    display: flex;
    align-items: center;
    justify-content: center;
  }
  .band-top .brand-square { background: var(--paper); }
  .band-top .brand-name { color: var(--paper); }
  .contact {
    flex: 1;
    display: flex;
    flex-direction: column;
    align-items: center;
    justify-content: center;
    font-family: "Source Sans 3", sans-serif;
    color: var(--navy);
    text-align: center;
    line-height: 1.3;
  }
  .contact-name {
    font-weight: 700;
    font-size: 18px;
    text-transform: uppercase;
    letter-spacing: 0.3px;
  }
  .contact-line { font-size: 14.5px; }
  .contact-label { font-weight: 700; }
  .band-bottom {
    height: 46px;
    background: var(--navy-deep);
    display: flex;
    align-items: center;
    justify-content: center;
    font-family: "Source Sans 3", sans-serif;
    font-weight: 700;
    font-size: 15px;
    letter-spacing: 3.5px;
    color: var(--paper);
    text-transform: uppercase;
  }
</style>
</head>
<body>
<main class="canvas">
  <section class="card card-front">
    <div class="brand">
      <span class="brand-square"></span>
      <span class="brand-name">Ferncliff Advisory</span>
    </div>
  </section>

  <section class="card card-back">
    <div class="band-top">
      <div class="brand">
        <span class="brand-square"></span>
        <span class="brand-name">Ferncliff Advisory</span>
      </div>
    </div>
    <div class="contact">
      <p class="contact-name">Daniel Whitcombe</p>
      <p class="contact-line">2870 North 9th Avenue, Summit Floor, Elm Ridge, Illinois 60531</p>
      <p class="contact-line"><span class="contact-label">Email:</span> dan@ferncliffadvisory.com</p>
    </div>
    <div class="band-bottom">www.ferncliffadvisory.com</div>
  </section>
</main>
</body>
</html>
```